Looking for a cool & simple business-card-design for digital agency

Hi!

We are a web agency that offers Reputation Management, Vextor & Seo Services and software development. We like cool things, we like innovative styles.

We have uploaded our logo.

Project Deadline Extended Reason: Client does not want any designs with the colorful logo. Please send us submissions ONLY with the blac and white logo. What the client would like to see:1) Back of the card: is a silver logo on a black background2) front of the card with all the data, please use white background and black logo thank you Added Friday, May 8, 2015

Industry/Entity Type

Software

```html
<!DOCTYPE html>
<html lang="en">
<head>
<meta charset="utf-8">
<title>Netvanta Business Card</title>
<link rel="stylesheet" href="https://fonts.googleapis.com/css2?family=Open+Sans:wght@400;600;700&display=swap">
<style>
  :root {
    --backdrop: #d9d9d9;
    --card: #fbfbfb;
    --card-dark: #141414;
    --silver: #c4c6c8;
    --ink: #1c1c1c;
    --teal: #1f9e9a;
    --band-1: #1fb5a8;
    --band-2: #6cbd3a;
    --band-3: #e6197a;
    --band-4: #ffd400;
  }
  * { box-sizing: border-box; margin: 0; padding: 0; }
  html, body {
    width: 1200px;
    height: 852px;
    overflow: hidden;
    background: var(--backdrop);
    font-family: "Open Sans", Arial, sans-serif;
  }
  .sheet {
    position: relative;
    width: 1200px;
    height: 852px;
  }
  .card {
    position: absolute;
    top: 276px;
    width: 520px;
    height: 300px;
    background: var(--card);
    border-radius: 10px;
    box-shadow: 0 6px 18px rgba(0,0,0,0.18);
    overflow: hidden;
  }
  .card--brand {
    left: 50px;
    background: var(--card-dark);
  }
  .card--contact { left: 630px; }

  /* Brand side: silver logo on black */
  .brand-lockup {
    position: absolute;
    inset: 0;
    display: flex;
    flex-direction: column;
    align-items: center;
    justify-content: center;
  }
  .brand-row {
    display: flex;
    align-items: center;
    gap: 14px;
  }
  .brand-mark {
    width: 26px;
    height: 26px;
    background: var(--ink);
    border-radius: 50%;
  }
  .brand-name {
    font-weight: 700;
    font-size: 52px;
    letter-spacing: 1px;
    color: var(--ink);
    line-height: 1;
  }
  .brand-tagline {
    margin-top: 10px;
    margin-left: 40px;
    font-size: 14px;
    letter-spacing: 6px;
    color: var(--ink);
  }
  .card--brand .brand-mark { background: var(--silver); }
  .card--brand .brand-name,
  .card--brand .brand-tagline { color: var(--silver); }

  /* Contact side: black logo on white */
  .person {
    position: absolute;
    left: 34px;
    top: 34px;
  }
  .person__name {
    font-size: 20px;
    font-weight: 700;
    color: var(--teal);
    line-height: 1.2;
  }
  .person__role {
    font-size: 12px;
    color: var(--ink);
  }
  .contact-list {
    position: absolute;
    left: 34px;
    bottom: 28px;
    list-style: none;
  }
  .contact-list li {
    display: flex;
    align-items: center;
    gap: 10px;
    font-size: 14px;
    color: var(--ink);
    line-height: 22px;
  }
  .contact-icon {
    width: 13px;
    height: 13px;
    fill: var(--teal);
    flex: none;
  }
  .contact-brand {
    position: absolute;
    right: 30px;
    top: 96px;
    text-align: right;
  }
  .contact-brand .brand-row { justify-content: flex-end; gap: 10px; }
  .contact-brand .brand-mark { width: 20px; height: 20px; }
  .contact-brand .brand-name { font-size: 34px; }
  .contact-brand .brand-tagline { font-size: 10px; letter-spacing: 4px; margin: 6px 0 0; }
  .edge-band {
    position: absolute;
    right: 0;
    bottom: 0;
    width: 210px;
    height: 8px;
    background: linear-gradient(90deg, var(--band-1), var(--band-2), var(--band-3), var(--band-4));
  }
</style>
</head>
<body>
<main class="sheet">

  <section class="card card--brand" aria-label="Card back">
    <div class="brand-lockup">
      <div class="brand-row">
        <span class="brand-mark"></span>
        <span class="brand-name">Netvanta</span>
      </div>
      <div class="brand-tagline">DIGITALE STRATEGIEN</div>
    </div>
  </section>

  <section class="card card--contact" aria-label="Card front">
    <div class="person">
      <div class="person__name">Your Long Name</div>
      <div class="person__role">Managing Director</div>
    </div>

    <ul class="contact-list">
      <li>
        <svg class="contact-icon" viewBox="0 0 16 16"><path d="M3 1h3l1 4-2 1c1 2 3 4 5 5l1-2 4 1v3c0 1-1 2-2 2C7 15 1 9 1 3c0-1 1-2 2-2z"/></svg>
        00.00.00.0000
      </li>
      <li>
        <svg class="contact-icon" viewBox="0 0 16 16"><path d="M4 1h8v4H4zM1 6h14v6h-3v3H4v-3H1zM5 10v4h6v-4z"/></svg>
        00.00.00.0000
      </li>
      <li>
        <svg class="contact-icon" viewBox="0 0 16 16"><path d="M1 3h14v10H1zM2 4l6 5 6-5v-0.5H2z" fill-rule="evenodd"/></svg>
        www.yourwebsite.com
      </li>
      <li>
        <svg class="contact-icon" viewBox="0 0 16 16"><circle cx="8" cy="8" r="7"/><path d="M1 8h14M8 1c3 3 3 11 0 14M8 1c-3 3-3 11 0 14" stroke="#fbfbfb" stroke-width="1" fill="none"/></svg>
        yourname@yourwebsite.com
      </li>
      <li class="address">Your Commercial or office address</li>
    </ul>

    <div class="contact-brand">
      <div class="brand-row">
        <span class="brand-mark"></span>
        <span class="brand-name">Netvanta</span>
      </div>
      <div class="brand-tagline">DIGITALE STRATEGIEN</div>
    </div>

    <div class="edge-band"></div>
  </section>

</main>
</body>
</html>
```